New Webpage for High Class Expert Witness Services Company

We are looking for a minimalist design for a webpage that just has our logo and an entry form offer to connect with one of our Liaisons.
The entry form should just ask for Name, Email, Contact Info and Description of Project.

Company Name is: The Marlowe Crest Advisory Services

Number of Pages Required

1 page

```html
<!DOCTYPE html>
<html lang="en">
<head>
<meta charset="UTF-8">
<title>The Marlowe Crest Advisory Services — Expert Witness Liaison</title>
<link href="https://fonts.googleapis.com/css2?family=Cinzel:wght@400;700&family=Montserrat:wght@400;500&display=swap" rel="stylesheet">
<style>
  :root {
    --bg-deep: #050505;
    --bg-mid: #1a1a1a;
    --silver: #d9d9d9;
    --silver-dark: #a9a9ad;
    --text: #f2f2f2;
    --field-border: #3a3a3a;
    --card-border: #555555;
    --button-top: #f0f0f0;
    --button-bottom: #a8a8ac;
    --button-text: #111111;
  }
  * { box-sizing: border-box; margin: 0; padding: 0; }
  html, body {
    width: 1110px;
    height: 1200px;
    overflow: hidden;
  }
  body {
    position: relative;
    background:
      radial-gradient(ellipse 600px 200px at 900px 60px, rgba(255,255,255,0.06), transparent 70%),
      radial-gradient(ellipse 500px 160px at 60px 700px, rgba(255,255,255,0.07), transparent 70%),
      linear-gradient(160deg, var(--bg-mid) 0%, #0c0c0c 45%, var(--bg-deep) 75%, #151515 100%);
    color: var(--text);
    font-family: "Montserrat", sans-serif;
  }
  .brand {
    position: absolute;
    top: 108px;
    left: 0;
    width: 1110px;
    text-align: center;
    font-family: "Cinzel", serif;
    font-weight: 400;
    font-size: 31px;
    letter-spacing: 2px;
    color: var(--silver);
  }
  .headline {
    position: absolute;
    top: 262px;
    left: 0;
    width: 1110px;
    text-align: center;
    font-family: "Cinzel", serif;
    font-weight: 700;
    font-size: 40px;
    line-height: 52px;
    color: var(--silver);
  }
  .headline-rule {
    position: absolute;
    top: 379px;
    left: 472px;
    width: 167px;
    height: 2px;
    background: var(--silver);
  }
  .intro {
    position: absolute;
    top: 411px;
    left: 0;
    width: 1110px;
    text-align: center;
    font-size: 22px;
    line-height: 29px;
    color: var(--text);
  }
  .consult-card {
    position: absolute;
    top: 514px;
    left: 135px;
    width: 840px;
    height: 561px;
    border: 1px solid var(--card-border);
    border-radius: 14px;
    background: linear-gradient(170deg, #262626 0%, #0a0a0a 55%, #141414 100%);
    box-shadow: 0 10px 30px rgba(0,0,0,0.6);
  }
  .field {
    position: absolute;
    left: 41px;
    width: 757px;
    height: 77px;
    border: 1px solid var(--field-border);
    border-radius: 7px;
    background: rgba(0,0,0,0.25);
    color: var(--text);
    font-family: "Montserrat", sans-serif;
    font-weight: 500;
    font-size: 15px;
    padding: 0 37px;
    outline: none;
  }
  .field::placeholder { color: var(--text); opacity: 1; }
  .field-name { top: 49px; }
  .field-email { top: 138px; }
  .field-contact { top: 229px; }
  .field-description {
    top: 318px;
    height: 117px;
    padding-top: 27px;
    resize: none;
  }
  .submit-button {
    position: absolute;
    top: 467px;
    left: 313px;
    width: 214px;
    height: 43px;
    border: none;
    border-radius: 4px;
    background: linear-gradient(180deg, var(--button-top), var(--button-bottom));
    color: var(--button-text);
    font-family: "Montserrat", sans-serif;
    font-weight: 500;
    font-size: 15px;
    cursor: pointer;
  }
  .footer-rule {
    position: absolute;
    top: 1150px;
    left: 15px;
    width: 1080px;
    height: 1px;
    background: linear-gradient(90deg, transparent, #555 15%, #555 85%, transparent);
  }
  .footer-note {
    position: absolute;
    top: 1170px;
    left: 0;
    width: 1110px;
    text-align: center;
    font-size: 13px;
    color: var(--silver);
  }
</style>
</head>
<body>
  <header class="brand">The Marlowe Crest Advisory Services</header>

  <h1 class="headline">GET CONNECTED WITH AN EXPERT<br>WITNESS LIAISON</h1>
  <div class="headline-rule"></div>

  <p class="intro">Connecting you with vetted medical experts—accurately, efficiently,<br>and with complete confidentiality.</p>

  <form class="consult-card">
    <input class="field field-name" type="text" placeholder="Name">
    <input class="field field-email" type="email" placeholder="Email">
    <input class="field field-contact" type="text" placeholder="Contact Info">
    <textarea class="field field-description" placeholder="Description of Project."></textarea>
    <button class="submit-button" type="submit">Request Consultation</button>
  </form>

  <div class="footer-rule"></div>
  <footer class="footer-note">Copyright © 2026 MARLOWE CREST. All rights reserved.</footer>
</body>
</html>
```